Business Cards - Brightpath Horizon

need to design unique business card for my mortgage business. I need to design credit card style business card for my business or any unique idea that you might have

Target Market(s)

Home Loan customers

Industry/Entity Type

Mortgage Brokerage

Contact Information for Business Card

please design credit card style or very unique style business card

Colors

Designer to choose colors to be used in the design.

Requirements
Must have
• Name
• position
• Phone number
• fax number
• email address
• website address
• social media address
• All above fields will be provided once design in finalised

```html
<!DOCTYPE html>
<html lang="en">
<head>
<meta charset="utf-8">
<title>Brightpath Horizon – Business Card</title>
<link rel="stylesheet" href="https://fonts.googleapis.com/css2?family=Arimo:wght@400&family=PT+Serif:wght@400;700&display=swap">
<style>
  :root {
    --backdrop: #2b2b2b;
    --card-white: #f4f4f4;
    --brand-blue: #0730c6;
    --brand-orange: #f7891f;
    --text-grey: #555555;
    --white: #ffffff;
  }
  html, body {
    margin: 0;
    padding: 0;
    width: 1200px;
    height: 960px;
    overflow: hidden;
    background: var(--backdrop);
  }
  .canvas {
    position: relative;
    width: 1200px;
    height: 960px;
  }
  .card {
    position: absolute;
    width: 600px;
    height: 343px;
    box-sizing: border-box;
  }
  .card--front {
    left: 314px;
    top: 113px;
    background: var(--card-white);
  }
  .card--back {
    left: 311px;
    top: 472px;
    background: var(--brand-blue);
  }

  /* Front */
  .brand-name {
    position: absolute;
    display: flex;
    align-items: center;
    gap: 10px;
    font-family: "PT Serif", Georgia, serif;
    font-weight: 700;
    white-space: nowrap;
  }
  .brand-name__dot {
    display: block;
    border-radius: 50%;
  }
  .card--front .brand-name {
    right: 37px;
    top: 70px;
    font-size: 27px;
    color: var(--brand-blue);
  }
  .card--front .brand-name__dot {
    width: 22px;
    height: 22px;
    background: var(--brand-orange);
  }
  .main-phone {
    position: absolute;
    right: 37px;
    top: 132px;
    margin: 0;
    font-family: "Arimo", Arial, sans-serif;
    font-size: 32px;
    color: var(--brand-blue);
    letter-spacing: 0.5px;
  }
  .holder {
    position: absolute;
    left: 34px;
    top: 206px;
  }
  .holder__name {
    margin: 0;
    font-family: "PT Serif", Georgia, serif;
    font-weight: 700;
    font-size: 20px;
    line-height: 24px;
    color: var(--brand-blue);
  }
  .holder__title {
    margin: 2px 0 0;
    font-family: "PT Serif", Georgia, serif;
    font-weight: 700;
    font-size: 15px;
    line-height: 18px;
    color: var(--brand-orange);
  }
  .holder__rule {
    width: 32px;
    height: 2px;
    margin: 7px 0 0;
    border: 0;
    background: var(--brand-blue);
  }
  .contact-list, .address {
    position: absolute;
    margin: 0;
    font-family: "PT Serif", Georgia, serif;
    font-size: 14px;
    line-height: 19px;
    color: var(--text-grey);
    font-style: normal;
  }
  .contact-list {
    left: 34px;
    top: 264px;
    padding: 0;
    list-style: none;
  }
  .address {
    left: 211px;
    top: 286px;
  }

  /* Back */
  .card--back .brand-name {
    left: 50%;
    top: 126px;
    transform: translateX(-50%);
    font-size: 40px;
    color: var(--white);
  }
  .card--back .brand-name__dot {
    width: 30px;
    height: 30px;
    background: var(--white);
  }
  .social-row {
    position: absolute;
    left: 0;
    top: 290px;
    width: 600px;
  }
</style>
</head>
<body>
<main class="canvas">
  <section class="card card--front" aria-label="Card front">
    <div class="brand-name">
      <span class="brand-name__dot"></span>
      <span>Brightpath Horizon</span>
    </div>
    <p class="main-phone">415 203 7761</p>

    <div class="holder">
      <h1 class="holder__name">DANIEL REYES</h1>
      <p class="holder__title">CEO/FOUNDER</p>
      <hr class="holder__rule">
    </div>
    <ul class="contact-list">
      <li>P. 415 203 7762</li>
      <li>daniel@brightpathhz.com</li>
      <li>www.brightpathhz.com</li>
    </ul>
    <address class="address">
      2140 Harbor View Road<br>
      Juneau, Alaska 99801
    </address>
  </section>

  <section class="card card--back" aria-label="Card back">
    <div class="brand-name">
      <span class="brand-name__dot"></span>
      <span>Brightpath Horizon</span>
    </div>
    <svg class="social-row" width="600" height="30" viewBox="0 0 600 30" aria-label="Social media links">
      <defs>
        <linearGradient id="rule-left" x1="0" x2="1" y1="0" y2="0">
          <stop offset="0" stop-color="#ffffff" stop-opacity="0"/>
          <stop offset="1" stop-color="#ffffff" stop-opacity="0.9"/>
        </linearGradient>
        <linearGradient id="rule-right" x1="0" x2="1" y1="0" y2="0">
          <stop offset="0" stop-color="#ffffff" stop-opacity="0.9"/>
          <stop offset="1" stop-color="#ffffff" stop-opacity="0"/>
        </linearGradient>
      </defs>
      <rect x="66" y="14" width="162" height="1.5" fill="url(#rule-left)"/>
      <rect x="374" y="14" width="164" height="1.5" fill="url(#rule-right)"/>
      <circle cx="251" cy="15" r="14" fill="#ffffff"/>
      <circle cx="282" cy="15" r="14" fill="#ffffff"/>
      <circle cx="316" cy="15" r="14" fill="#ffffff"/>
      <circle cx="349" cy="15" r="14" fill="#ffffff"/>
    </svg>
  </section>
</main>
</body>
</html>
```